Coffeeshop menu for filter tip

We want to have a cannabis (coffeeshop) menu in the size 25mm wide x 60mm wide. Some examples attached.

it must have the following text:
Menu

WEED p/g
Oblivane €16
Cloudplum €14
Tide Runner €14
Quincefig €16
Mega Marsh €14
Grey Heron €14

HASH p/g
Tashar Amber €12
Pebble Frost€11
Lime Dunes €14
Ash Petal €10

Target Market(s)

tourist in Amsterdam

Requirements
Nice to have
• cannabis sign leaf
• No Cigarettes allowed symbol

```html
<!DOCTYPE html>
<html lang="en">
<head>
<meta charset="utf-8">
<title>Amsterdam Menu</title>
<link rel="stylesheet" href="https://fonts.googleapis.com/css2?family=Righteous&family=Quicksand:wght@700&family=Playfair+Display:ital@1&family=Rubik+Mono+One&display=swap">
<style>
  :root {
    --bg: #2c2c2c;
    --brush: #3a3a3a;
    --leaf: #242424;
    --white: #f1f1f1;
    --orange: #f2a024;
    --gold: #a77a3c;
    --red: #d62a2a;
  }
  * { margin: 0; padding: 0; box-sizing: border-box; }
  html, body { width: 1200px; height: 2877px; overflow: hidden; background: var(--bg); }
  .menu-card { position: relative; width: 1200px; height: 2877px; background: var(--bg); overflow: hidden; }

  .brush-texture {
    position: absolute; left: 300px; top: 230px; width: 860px; height: 2600px;
    background: linear-gradient(175deg, rgba(70,70,70,0.55) 0%, rgba(60,60,60,0.35) 50%, rgba(50,50,50,0.1) 100%);
    border-radius: 40% 30% 20% 40%;
  }
  .leaf-decoration {
    position: absolute; left: 720px; top: 1980px; width: 480px; height: 720px;
    background: radial-gradient(ellipse at center, var(--leaf) 0%, rgba(36,36,36,0.6) 50%, rgba(36,36,36,0) 75%);
  }

  .title-frame {
    position: absolute; left: 170px; top: 127px; width: 890px; height: 331px;
    border: 5px solid var(--gold);
    text-align: center; color: var(--white);
  }
  .title-city {
    position: absolute; left: 0; right: 0; top: 36px;
    font-family: "Righteous", sans-serif; font-size: 84px; letter-spacing: 12px; line-height: 1;
  }
  .title-menu {
    position: absolute; left: 0; right: 0; top: 138px;
    font-family: "Rubik Mono One", sans-serif; font-size: 150px; letter-spacing: 40px; line-height: 1;
    padding-left: 40px; opacity: 0.92;
  }

  .section-head {
    position: absolute; left: 161px; width: 899px;
    display: flex; justify-content: space-between; align-items: baseline; color: var(--orange);
  }
  .section-name { font-family: "Righteous", sans-serif; font-size: 100px; letter-spacing: 8px; line-height: 1; }
  .section-unit { font-family: "Playfair Display", serif; font-style: italic; font-size: 96px; line-height: 1; }

  .price-list { position: absolute; left: 161px; width: 899px; list-style: none; }
  .price-row {
    display: flex; align-items: baseline; height: 92px;
    font-family: "Quicksand", sans-serif; font-weight: 700; font-size: 62px; letter-spacing: 5px;
    color: var(--white); text-transform: uppercase; line-height: 1;
  }
  .leader {
    flex: 1; height: 8px; margin: 0 14px;
    background: radial-gradient(circle, var(--white) 3px, transparent 3.5px) 0 0 / 20px 8px repeat-x;
  }

  .no-smoking { position: absolute; left: 182px; top: 2450px; width: 230px; height: 230px; }
  .no-smoking-label {
    position: absolute; left: 479px; top: 2540px;
    font-family: "Quicksand", sans-serif; font-weight: 700; font-size: 62px; letter-spacing: 2px; color: var(--white);
  }
</style>
</head>
<body>
<main class="menu-card">
  <div class="brush-texture" role="img" aria-label="Grey brush stroke texture"></div>
  <div class="leaf-decoration" role="img" aria-label="Faint cannabis leaf"></div>

  <header class="title-frame">
    <div class="title-city">AMSTERDAM</div>
    <h1 class="title-menu">MENU</h1>
  </header>

  <div class="section-head" style="top:690px"><h2 class="section-name">WEED</h2><span class="section-unit">p/g</span></div>
  <ul class="price-list" style="top:855px">
    <li class="price-row"><span>Oblivane</span><span class="leader"></span><span>€16</span></li>
    <li class="price-row"><span>Cloudplum</span><span class="leader"></span><span>€14</span></li>
    <li class="price-row"><span>Tide Runner</span><span class="leader"></span><span>€14</span></li>
    <li class="price-row"><span>Quincefig</span><span class="leader"></span><span>€16</span></li>
    <li class="price-row"><span>Mega Marsh</span><span class="leader"></span><span>€14</span></li>
    <li class="price-row"><span>Grey Heron</span><span class="leader"></span><span>€14</span></li>
  </ul>

  <div class="section-head" style="top:1630px"><h2 class="section-name">HASH</h2><span class="section-unit">p/g</span></div>
  <ul class="price-list" style="top:1810px">
    <li class="price-row"><span>Tashar Amber</span><span class="leader"></span><span>€12</span></li>
    <li class="price-row"><span>Pebble Frost</span><span class="leader"></span><span>€11</span></li>
    <li class="price-row"><span>Lime Dunes</span><span class="leader"></span><span>€14</span></li>
    <li class="price-row"><span>Ash Petal</span><span class="leader"></span><span>€10</span></li>
  </ul>

  <svg class="no-smoking" viewBox="0 0 230 230" aria-label="No smoking symbol">
    <circle cx="115" cy="115" r="108" fill="#ffffff"/>
    <rect x="30" y="110" width="130" height="28" fill="#1e1e1e"/>
    <rect x="160" y="110" width="30" height="28" fill="#1e1e1e" opacity="0.75"/>
    <path d="M172 100 q-10 -20 5 -40 q12 -16 0 -34" fill="none" stroke="#1e1e1e" stroke-width="7"/>
    <circle cx="115" cy="115" r="100" fill="none" stroke="var(--red)" stroke-width="18"/>
    <line x1="45" y1="45" x2="185" y2="185" stroke="var(--red)" stroke-width="18"/>
  </svg>
  <p class="no-smoking-label">NO CIGARETTES</p>
</main>
</body>
</html>
```